Business Cards for IT Consulting Company (Managed Service Provider)

I am looking to have some business cards printed and would like some designs. We are an IT Consulting company based in Vancouver BC. I would like a nice clean and modern look to the cards. I have uploaded all the versions of my logo so parts can be used as needed. Here is a snippit from our website homepage:

Quillbrook Networks Ltd. is an IT Solutions Partner located in Vancouver BC, Canada. We offer IT solutions and support to customers in the greater Vancouver Area. With expertise in Microsoft platforms, as well as Linux and Mac OSX and over 12 years experience in the IT industry, Quillbrook Networks is dedicated to offering our clients top quality service and products. We take pride in the solutions we offer our customers. The greatest compliment a client can give us is to recommend our services.

Quillbrook Networks Ltd. offers a wide range of IT services from onsite service to remote support and managed service solutions. This allows clients to choose the support path that best suits their company’s needs. Supporting many different sized companies from small to enterprise level over the past 12 years Quillbrook Networks has the experience and expertise needed to ensure things run smoothly. Allowing our clients to focus on doing business.

Revolutionizing the way IT services are delivered.

Quillbrook Networks is dedicated to providing our clients with IT solutions that work and grow with them for years to come. This philosophy helps save money in the long run instead of replacing equipment constantly. Far too often IT solutions are not well thought out and while possibly solving the problem at hand, require replacement due to growth or quality within a very short time frame. Quillbrook Networks takes pride in providing solutions that will last and be able to accommodate growth without the need for replacement.

Industry/Entity Type

Information Technology

Contact Information for Business Card

Quillbrook Networks Ltd.
(Employee Name)
Eml: (Employees Email Address)
Web: quillbrook.me
Ph: 604-555-0148

Font styles to use
Serif
Sans Serif

Requirements
Must have
• The Company logo and company colors.
Nice to have
• - Our tag line: "Revolutionizing IT Services" or "Revolutionizing the way IT services are delivered."
• - Also I really like the idea of nature and technology together blending which is sort of where my logo came from so integrating that somehow onto the business cards would be great.

```html
<!DOCTYPE html>
<html lang="en">
<head>
<meta charset="utf-8">
<title>Quillbrook Networks Ltd. – Business Card</title>
<link href="https://fonts.googleapis.com/css2?family=Montserrat:wght@400;500;600;700&display=swap" rel="stylesheet">
<style>
  :root {
    --stage: #2b2b2b;
    --card-black: #000000;
    --brand-blue: #00a9e8;
    --white: #ffffff;
  }
  * { margin: 0; padding: 0; box-sizing: border-box; }
  html, body {
    width: 1200px; height: 900px; overflow: hidden;
    background: var(--stage);
    font-family: "Montserrat", sans-serif;
  }
  .card {
    position: absolute; left: 260px;
    width: 680px; height: 388px;
    background: var(--card-black);
    overflow: hidden;
  }
  .card-front { top: 50px; }
  .card-back { top: 470px; }

  /* Front */
  .front-name {
    position: absolute; left: 0; right: 0; top: 120px;
    text-align: center; color: var(--brand-blue);
    font-size: 40px; font-weight: 600; letter-spacing: 1px;
  }
  .front-rule {
    position: absolute; left: 0; right: 0; top: 300px;
    height: 1px; background: var(--brand-blue);
  }
  .tagline {
    position: absolute; left: 50%; top: 290px; transform: translateX(-50%);
    padding: 0 14px; background: var(--card-black);
    color: var(--white); font-size: 17px; font-weight: 500; letter-spacing: 1px;
    white-space: nowrap;
  }

  /* Back */
  .side-strip {
    position: absolute; left: 28px; top: 0; width: 52px; height: 388px;
    background: var(--white);
  }
  .brand-square {
    position: absolute; left: 40px; top: 168px; width: 44px; height: 44px;
    background: var(--brand-blue);
  }
  .company-name {
    position: absolute; left: 104px; top: 170px;
    color: var(--white); font-size: 32px; font-weight: 600; white-space: nowrap;
  }
  .band-divider {
    position: absolute; left: 80px; right: 0; top: 222px;
    height: 2px; background: var(--white);
  }
  .contact-band {
    position: absolute; left: 80px; right: 0; top: 230px; bottom: 0;
    background: var(--brand-blue);
  }
  .person {
    position: absolute; right: 34px; top: 16px; text-align: right; color: var(--white);
  }
  .person-name { font-size: 22px; font-weight: 700; letter-spacing: 1px; }
  .person-title {
    font-size: 11px; font-weight: 500; letter-spacing: 1.5px;
    border-top: 1px solid var(--white); padding-top: 3px; margin-top: 4px;
    padding-left: 300px;
  }
  .contact-list {
    position: absolute; left: 30px; top: 72px; list-style: none;
    border-top: 1px solid var(--white); padding-top: 10px; width: 300px;
  }
  .contact-list li {
    display: flex; align-items: center; gap: 10px;
    color: var(--white); font-size: 14px; font-weight: 500; letter-spacing: 0.5px;
    line-height: 22px;
  }
  .contact-list svg { width: 12px; height: 12px; fill: none; stroke: var(--white); stroke-width: 1.6; }
</style>
</head>
<body>
  <section class="card card-front">
    <div class="front-name">Quillbrook Networks</div>
    <div class="front-rule"></div>
    <div class="tagline">Revolutionizing IT Services</div>
  </section>

  <section class="card card-back">
    <div class="side-strip"></div>
    <div class="brand-square"></div>
    <div class="company-name">Quillbrook Networks Ltd.</div>
    <div class="band-divider"></div>
    <div class="contact-band">
      <div class="person">
        <div class="person-name">MARLOW HENSLEY</div>
        <div class="person-title">DIRECTOR</div>
      </div>
      <ul class="contact-list">
        <li>
          <svg viewBox="0 0 12 12"><path d="M2 1.5h2.5l1 2.5-1.5 1a6 6 0 0 0 3 3l1-1.5 2.5 1V10a1 1 0 0 1-1 1A9 9 0 0 1 1 2.5a1 1 0 0 1 1-1z"/></svg>
          604-555-0148
        </li>
        <li>
          <svg viewBox="0 0 12 12"><rect x="1" y="2.5" width="10" height="7"/><path d="M1 2.5l5 4 5-4"/></svg>
          info@marlowhensley.com
        </li>
        <li>
          <svg viewBox="0 0 12 12"><circle cx="6" cy="6" r="5"/><path d="M1 6h10M6 1c2.5 3 2.5 7 0 10M6 1c-2.5 3-2.5 7 0 10"/></svg>
          www.quillbrook.me
        </li>
      </ul>
    </div>
  </section>
</body>
</html>
```